Desktop and Networking Support Course 9.17.25

Important the ad should not be very busy with the text taking up the major part of the ad .. please do not make the text so big that it takes up most of the ad..
Flyer Design Brief for Graphic Artist
also i am looking for something unique or creative that it will stand out .
Size & Layout:
Full Page with Bleed: 8” x 10.75” + 0.25” bleed on all sides.
Footer Space: Leave a 1-inch margin at the bottom for footer content (e.g., contact info, logo, or call-to-action).
Target Audience:
College-age students (around 24 years old)
Located in the USA
Interested in creative, professional, and career-building opportunities
Purpose:
To attract students to enroll in a college program
Flyer should be eye-catching, unique, and creative
Text must be clear and readable,
Design Style:
Use vector art, typography, or photography — your choice
If using photography, feature a white young professional USA citizen:
Wearing a white collared shirt
not with long hair
Creative Direction:
The flyer should stand out visually — something people would want to look at and keep
Showcase creativity and professionalism
Use bold colors, dynamic layout, or unexpected design elements to grab attention
Avoid clutter — keep the design balanced and clean
Text Suggestions (can be adjusted):
Footer,
please leave one inch on the bottom for the footer

```html
<!DOCTYPE html>
<html lang="en">
<head>
<meta charset="utf-8">
<title>Desktop &amp; Network Support Course Flyer</title>
<link href="https://fonts.googleapis.com/css2?family=Bebas+Neue&family=Montserrat:wght@500;600;700;800&display=swap" rel="stylesheet">
<style>
  :root {
    --ink: #2b2b2b;
    --panel: #2e2e2e;
    --grey-text: #8a8a8a;
    --grey-soft: #a3a3a3;
    --paper: #ececec;
    --white: #ffffff;
    --footer: #ffffff;
    --rule: #8a8a8a;
  }
  * { margin: 0; padding: 0; box-sizing: border-box; }
  html, body { width: 901px; height: 1200px; overflow: hidden; background: var(--footer); }
  .flyer {
    position: relative; width: 901px; height: 1200px; overflow: hidden;
    font-family: "Montserrat", sans-serif; color: var(--ink);
    background: var(--footer);
  }
  .hero-bg {
    position: absolute; left: 0; top: 0; width: 901px; height: 1021px;
    background: radial-gradient(circle at 100% 10%, #f6f6f6 0%, var(--paper) 70%);
  }
  .headline { position: absolute; left: 61px; top: 56px; }
  .headline .soft { display: block; font-weight: 800; font-size: 60px; line-height: 62px; color: var(--grey-text); letter-spacing: -1px; }
  .headline .career { display: block; font-family: "Bebas Neue", sans-serif; font-size: 164px; line-height: 134px; color: var(--ink); margin: 0 0 -4px -3px; letter-spacing: 1px; }
  .click-pill {
    position: absolute; left: 60px; top: 317px; width: 320px; height: 62px;
    background: var(--panel); border-radius: 31px; display: flex; align-items: center;
    padding-left: 26px; gap: 14px; color: var(--white); font-weight: 700; font-size: 36px;
    box-shadow: 4px 6px 10px rgba(0,0,0,0.25);
  }
  .course-title { position: absolute; left: 62px; top: 402px; font-weight: 700; font-size: 24px; color: var(--ink); }
  .course-title span { color: var(--grey-text); }
  .info-panel {
    position: absolute; left: 60px; top: 451px; width: 700px; height: 570px;
    background: var(--panel); border-radius: 46px 0 0 46px;
  }
  .model-photo {
    position: absolute; left: 585px; top: 57px; width: 264px; height: 962px;
    background: linear-gradient(180deg, #f4f4f4 0%, #e6e6e6 55%, #9a9a9a 56%, #8c8c8c 92%, #2a2a2a 100%);
    border-radius: 120px 120px 20px 20px;
  }
  .on-dark { color: var(--white); }
  .focus { position: absolute; left: 101px; top: 480px; font-weight: 700; font-size: 29px; line-height: 34px; }
  .focus .muted { color: var(--grey-soft); }
  .rule { position: absolute; left: 101px; width: 355px; border-top: 1px dashed var(--rule); }
  .stat-value { position: absolute; left: 99px; top: 580px; font-weight: 800; font-size: 78px; line-height: 80px; letter-spacing: -2px; }
  .stat-label { position: absolute; left: 101px; top: 663px; font-weight: 700; font-size: 17px; }
  .v-rule { position: absolute; left: 289px; top: 593px; height: 95px; border-left: 1px dashed var(--rule); }
  .class-label { position: absolute; left: 308px; top: 597px; font-weight: 700; font-size: 24px; }
  .year-pill {
    position: absolute; left: 306px; top: 636px; width: 116px; height: 37px; border-radius: 19px;
    background: var(--grey-text); color: var(--white); font-weight: 800; font-size: 23px;
    letter-spacing: 4px; text-align: center; line-height: 37px; padding-left: 4px;
    box-shadow: 3px 5px 8px rgba(0,0,0,0.35);
  }
  .ranking { position: absolute; left: 101px; top: 720px; font-weight: 700; font-size: 17px; line-height: 22px; }
  .benefits { position: absolute; left: 102px; top: 813px; list-style: none; }
  .benefits li { display: flex; align-items: center; gap: 8px; height: 40px; font-weight: 500; font-size: 18.5px; }
  .tag { position: absolute; top: 942px; height: 41px; border-radius: 21px; font-weight: 600; font-size: 14.5px; line-height: 41px; }
  .tag-format { left: 103px; width: 272px; background: var(--grey-text); color: var(--white); padding-left: 14px; }
  .tag-aid { left: 361px; width: 248px; background: var(--white); color: var(--ink); text-align: center; box-shadow: -4px 3px 8px rgba(0,0,0,0.3); }
</style>
</head>
<body>
<div class="flyer">
  <div class="hero-bg"></div>

  <h1 class="headline">
    <span class="soft">Your</span>
    <span class="career">CAREER</span>
    <span class="soft">Is Just a</span>
  </h1>

  <div class="click-pill">
    <svg width="28" height="42" viewBox="0 0 28 42" fill="none" stroke="#fff" stroke-width="1.8" stroke-linecap="round" stroke-linejoin="round" aria-hidden="true">
      <path d="M10 16V7a2.5 2.5 0 0 1 5 0v12"/>
      <path d="M15 18a2.3 2.3 0 0 1 4.6 0v3M19.6 20a2.3 2.3 0 0 1 4.6 0v9c0 6-3.5 10-9 10h-2c-4 0-6-2-8-6l-3-6a2.2 2.2 0 0 1 3.8-2.2L10 27V17"/>
      <path d="M12.5 1v2M6 3.5l1.4 1.4M19 3.5l-1.4 1.4M4 9h2M19 9h2"/>
    </svg>
    <span>Click Away</span>
  </div>

  <p class="course-title">Desktop &amp; Network <span>Support Course</span></p>

  <div class="info-panel"></div>
  <div class="model-photo" role="img" aria-label="Photo of a smiling young professional in a white shirt and grey trousers, pointing with his thumb"></div>

  <h2 class="focus on-dark">Master Fenestra<br><span class="muted">Operating Systems</span></h2>
  <div class="rule" style="top:575px"></div>

  <div class="stat-value on-dark">90%</div>
  <div class="stat-label on-dark">Employment Rate</div>
  <div class="v-rule"></div>
  <div class="class-label on-dark">Class Of</div>
  <div class="year-pill">2025</div>

  <div class="rule" style="top:705px"></div>
  <p class="ranking on-dark">Prepare for 3 of the Top 10 Tech Jobs<br>National Career Review 2025</p>
  <div class="rule" style="top:783px"></div>

  <ul class="benefits on-dark">
    <li><svg width="20" height="20" viewBox="0 0 20 20" fill="none" stroke="#bdbdbd" stroke-width="1.6" aria-hidden="true"><rect x="1" y="2" width="16" height="16" rx="2"/><path d="M5 10l3.5 3.5L19 3"/></svg>Hands-On Desktop &amp; Network Training</li>
    <li><svg width="20" height="20" viewBox="0 0 20 20" fill="none" stroke="#bdbdbd" stroke-width="1.6" aria-hidden="true"><rect x="1" y="2" width="16" height="16" rx="2"/><path d="M5 10l3.5 3.5L19 3"/></svg>Real-World Troubleshooting Skills</li>
    <li><svg width="20" height="20" viewBox="0 0 20 20" fill="none" stroke="#bdbdbd" stroke-width="1.6" aria-hidden="true"><rect x="1" y="2" width="16" height="16" rx="2"/><path d="M5 10l3.5 3.5L19 3"/></svg>Ready for IT Jobs</li>
  </ul>

  <div class="tag tag-format">In-Person and Remote Options</div>
  <div class="tag tag-aid">Partial Scholarships Offered</div>
</div>
</body>
</html>
```